Business card for medical clinic

I need an upmarket, modern medical/health business card for my clinic

Contact Information for Business Card

name, address, email, qr code

```html
<!DOCTYPE html>
<html lang="en">
<head>
<meta charset="utf-8">
<title>Lumera Care Group – Business Card</title>
<link href="https://fonts.googleapis.com/css2?family=Poppins:wght@300;400;500;700&display=swap" rel="stylesheet">
<style>
  :root {
    --page-bg: #d8cfc4;
    --card-bg: #ece3d7;
    --card-edge: #f6efe6;
    --teal-deep: #0c5b72;
    --teal: #1a7e95;
    --teal-light: #3a9fb2;
    --ink: #1f1d1b;
    --sand-text: #e4d8c8;
    --curve-dark: #2c3c4a;
  }
  * { box-sizing: border-box; margin: 0; padding: 0; }
  html, body { width: 1200px; height: 1046px; overflow: hidden; }
  body {
    background: var(--page-bg);
    font-family: "Poppins", sans-serif;
    position: relative;
  }
  .card {
    position: absolute;
    left: 80px; top: 240px;
    width: 1040px; height: 566px;
    border-radius: 36px;
    background: var(--card-bg);
    border: 2px solid var(--card-edge);
    overflow: hidden;
    box-shadow: 0 18px 40px rgba(60, 45, 30, 0.18);
  }
  .card__band { position: absolute; left: 0; top: 0; width: 100%; height: 100%; }
  .brand {
    position: absolute; left: 0; right: 0; top: 78px;
    display: flex; align-items: center; justify-content: center; gap: 18px;
  }
  .brand__dot {
    width: 30px; height: 30px; border-radius: 50%;
    background: var(--teal-deep);
  }
  .brand__name {
    font-weight: 500; font-size: 42px; letter-spacing: 1px;
    color: var(--teal-deep); line-height: 1;
  }
  .person {
    position: absolute; right: 584px; top: 300px;
    text-align: right;
  }
  .person__name { font-size: 46px; line-height: 1; color: var(--teal); letter-spacing: 1px; }
  .person__first { font-weight: 700; }
  .person__last { font-weight: 300; color: var(--teal-light); }
  .person__title { margin-top: 8px; font-size: 25px; font-weight: 500; color: var(--ink); }
  .divider {
    position: absolute; left: 523px; top: 277px;
    width: 2px; height: 152px; background: var(--teal-deep);
  }
  .contacts {
    position: absolute; left: 594px; top: 298px;
    list-style: none;
  }
  .contacts__item {
    display: flex; align-items: center; gap: 20px;
    height: 36px; font-size: 27px; color: var(--ink); letter-spacing: 0.5px;
  }
  .contacts__icon { width: 24px; height: 24px; flex: none; }
  .address {
    position: absolute; left: 0; right: 0; top: 500px;
    text-align: center; font-size: 25px; letter-spacing: 1px;
    color: var(--sand-text);
  }
</style>
</head>
<body>
  <div class="card">
    <svg class="card__band" viewBox="0 0 1040 566" preserveAspectRatio="none" aria-hidden="true">
      <defs>
        <linearGradient id="bandFill" x1="0" y1="0" x2="1" y2="0">
          <stop offset="0" stop-color="#1d7a90"/>
          <stop offset="0.45" stop-color="#2a8ea4"/>
          <stop offset="1" stop-color="#0d6880"/>
        </linearGradient>
      </defs>
      <path d="M0 400 Q520 560 1040 398 L1040 566 L0 566 Z" fill="url(#bandFill)"/>
      <path d="M0 400 Q520 560 1040 398" fill="none" stroke="#d9cbb8" stroke-width="5"/>
      <path d="M38 401 Q520 540 1002 400" fill="none" stroke="var(--curve-dark)" stroke-width="2.5"/>
    </svg>

    <div class="brand">
      <span class="brand__dot"></span>
      <span class="brand__name">Lumera Care Group</span>
    </div>

    <div class="person">
      <p class="person__name"><span class="person__first">Marta</span> <span class="person__last">Novelli</span></p>
      <p class="person__title">Founder &amp; CEO</p>
    </div>

    <div class="divider"></div>

    <ul class="contacts">
      <li class="contacts__item">
        <svg class="contacts__icon" viewBox="0 0 24 24"><path fill="var(--teal-deep)" d="M6.6 10.8a15 15 0 0 0 6.6 6.6l2.2-2.2a1 1 0 0 1 1-.25 11.4 11.4 0 0 0 3.6.57 1 1 0 0 1 1 1V20a1 1 0 0 1-1 1A17 17 0 0 1 3 4a1 1 0 0 1 1-1h3.5a1 1 0 0 1 1 1c0 1.25.2 2.45.57 3.57a1 1 0 0 1-.25 1z"/></svg>
        <span>(555) 214-0387</span>
      </li>
      <li class="contacts__item">
        <svg class="contacts__icon" viewBox="0 0 24 24"><rect x="2" y="5" width="20" height="14" rx="2" fill="none" stroke="var(--teal-deep)" stroke-width="2"/><path d="M3 6l9 7 9-7" fill="none" stroke="var(--teal-deep)" stroke-width="2"/></svg>
        <span>hello@lumeracare.com</span>
      </li>
      <li class="contacts__item">
        <svg class="contacts__icon" viewBox="0 0 24 24"><circle cx="12" cy="12" r="9.5" fill="none" stroke="var(--teal-deep)" stroke-width="2"/><path d="M2.5 12h19M12 2.5c3 3 3 16 0 19M12 2.5c-3 3-3 16 0 19" fill="none" stroke="var(--teal-deep)" stroke-width="1.6"/></svg>
        <span>www.lumeracare.com</span>
      </li>
    </ul>

    <p class="address">1480 Meadowbrook Ave. Suite 310 Springfield, IL 62704</p>
  </div>
</body>
</html>
```